Norvane Freight and Provision Service Brochure

Please see http://www.norvanefreight.example for who we are and what we do.
We would like to see a design that matches the industry we work in i.e. Oil and Gas. The design should communicate large, heavy field operations, supply of vast bulk fuel quantities to our US and Afghan Military customers, plus financial independence and the companies whatever it takes attitude operation in remote often hostile areas. Dark colors like on the website - contrasting our green logo. A strong focus on our past performance/past experience.

Target Market(s)

Military Customers, Partners, Subcontractors

Industry/Entity Type

Industry

Contact Information for Business Card

Display of Address, Phone, email etc. of our 4 offices

Font styles to use
Sans Serif

Requirements
Must have
• Glossy brochure, modern, cool design. Great display (map) of our offices in the Middle East, Europe and Central Asia. A focus on our past performance/past experience. Customer logos/references
Nice to have
• Prominent highlighted watermark logo
Should not have
• Standard A4/Letter brochure

```html
<!DOCTYPE html>
<html lang="en">
<head>
<meta charset="utf-8">
<title>Norvane Freight and Provision – Our Projects</title>
<link href="https://fonts.googleapis.com/css2?family=Montserrat:wght@600;700&family=Arimo:wght@400&display=swap" rel="stylesheet">
<style>
  :root{
    --backdrop:#e9e6e1;
    --panel:#54595b;
    --band:#2f6f91;
    --band-deep:#1f4f6c;
    --accent:#d6e41c;
    --text:#f2f2f2;
    --white:#ffffff;
  }
  *{margin:0;padding:0;box-sizing:border-box}
  html,body{width:1200px;height:579px;overflow:hidden;background:var(--backdrop)}
  .spread{position:absolute;left:25px;top:60px;width:1150px;height:462px;display:flex;box-shadow:0 2px 8px rgba(0,0,0,.25)}
  .page{position:relative;width:575px;height:462px;background:var(--panel);overflow:hidden}
  .photo{position:absolute}
  .hero-refinery{left:0;top:0;width:575px;height:135px;background:linear-gradient(180deg,#3c3a4a 0%,#b8744a 55%,#e5a052 70%,#2b2a2e 100%)}
  .band{position:absolute;left:0;width:575px;background:linear-gradient(180deg,var(--band) 0%,var(--band-deep) 100%)}
  .band-left{top:135px;height:73px}
  .band-right{top:278px;height:62px;background:linear-gradient(180deg,var(--band-deep) 0%,var(--band) 100%)}
  .hero-rig{left:0;top:340px;width:575px;height:122px;background:linear-gradient(180deg,#4d7fa2 0%,#7b6a58 45%,#c27a3a 70%,#2d4d66 100%)}
  .section-title{position:absolute;font:700 19.5px/1 "Montserrat",sans-serif;color:var(--white);letter-spacing:.2px}
  .project{position:absolute}
  .project-title{font:600 13.6px/16px "Montserrat",sans-serif;color:var(--accent)}
  .project-body{margin-top:5px;font:400 6.9px/8.6px "Arimo",sans-serif;letter-spacing:.12px;color:var(--text);text-align:justify}
  .thumb{position:absolute}
</style>
</head>
<body>
<div class="spread">
  <section class="page page-left">
    <div class="photo hero-refinery" role="img" aria-label="Refinery at dusk lit up along a waterfront"></div>
    <div class="band band-left"></div>
    <h2 class="section-title" style="left:33px;top:162px">OUR PROJECTS</h2>

    <div class="thumb" role="img" aria-label="Soldier refuelling an aircraft with a fuel nozzle" style="left:39px;top:249px;width:110px;height:48px;background:linear-gradient(135deg,#6a6258,#b7463c 50%,#3b3a36)"></div>
    <article class="project" style="left:157px;top:212px;width:406px">
      <h3 class="project-title">MoD - CAW Aviation Fuel Supply Contract - Contract<br>Number NV-4471-D-0011</h3>
      <p class="project-body">We are an incumbent contractor for this requirement of the Ministry of Defence of Carvella and we have performed our duties exceptionally well. This contract is the primary support mechanism for Carvellan Air Wing (CAW) requirements throughout the region and for all Direct-Into-Plane (Into-Aircraft) fuel requirements of the CAW. Norvane fulfils the Government requirements according to terms established in the basic contract and resulting delivery orders. We accomplish all required commodity sourcing and transportation services to delivery points specified in resulting requests for service on a on a free on board (F.O.B.) Destination basis.</p>
    </article>

    <div class="thumb" role="img" aria-label="Soldier holding a flag against the sky" style="left:39px;top:358px;width:110px;height:77px;background:linear-gradient(135deg,#1c2e52,#4a6a9c 55%,#7a2a26)"></div>
    <article class="project" style="left:157px;top:326px;width:406px">
      <h3 class="project-title">Bulk Diesel Supply to Kestrel Valley Power Plants -<br>Contract Number: NV-5582-C-0002</h3>
      <p class="project-body">The contract is a primary support mechanism for fuel requirements of the RPU Southern Bridging Scheme (SBS) power generation. It provides fuel for the operation of the two (2) diesel power plants built under the SBS program which are located at Halvern Industrial Park (HIP) and Ostmere (OST). The fuel will allow electrical power generation for Kestrel Valley while the Northern Grid Link (NGL) – Southern Grid Link (SGL) connector is being completed. Norvane accomplishes all required commodity sourcing and delivery to points specified in the contract on a free on board (F.O.B.) Destination basis. Norvane is responsible for a performance-based contracting relationship, where its customer the Government specifies the desired end-state and Norvane executes an effective ‘turn-key’ sourcing solution for required commodities and all transportation to the specified delivery locations.</p>
    </article>
  </section>

  <section class="page page-right">
    <div class="thumb" role="img" aria-label="Convoy of cargo trucks on a mountain road" style="left:23px;top:60px;width:82px;height:63px;background:linear-gradient(160deg,#8b8b7e,#4b4d45 60%,#6c6a5c)"></div>
    <article class="project" style="left:138px;top:20px;width:427px">
      <h3 class="project-title">Regional Transport Network (RTN) – South – Contract<br>Number NV-7160-D-R061</h3>
      <p class="project-body">The Regional Transport Network (RTN) uses a network of Government approved privately owned local trucking companies, otherwise known as Elder Owned Companies (EOCs) or locally-owned and locally-operated subcontractors. Norvane manages the approved EOCs or approved subcontractors to provide secure, reliable cargo and fuel transportation services to and from locations in the provinces of Varn, Oleska, Tammor, and Kestrel Valley without the use of convoy security. The use of RTN regional transportation companies capitalizes on existing business agreements to promote the development of new business agreements with influential regional leaders. This capitalization of existing business agreements into new areas and companies allows local infrastructure to develop, implement and sustain a locally-owned and operated transportation network capable of providing secure and reliable transportation of cargo.</p>
    </article>

    <div class="thumb" role="img" aria-label="Wide desert landscape with sand dunes" style="left:23px;top:180px;width:82px;height:78px;background:linear-gradient(170deg,#c9b79a,#a88a62 50%,#6e5a43)"></div>
    <article class="project" style="left:138px;top:144px;width:427px">
      <h3 class="project-title">National Field Trucking II – Contract Number<br>NV-7160-D-R049</h3>
      <p class="project-body">The principal contract supporting the regional supply chain is called National Field Trucking (NFT). Although there are other supply chain contracts, the NFT contracts provides trucking for over 70 percent of the total goods and materiel distributed to troops in the field. The trucks carry fuel, food, supplies, and heavy equipment. Norvane provides all management and logistics support resources necessary to pick-up cargo (material or equipment) at origin and delivers cargo to destination on Required Delivery Date (RDD) established by its customer. This includes proactive and competent management; well maintained logistics support resources, and trustworthy employees and subcontractors as necessary to facilitate dependable movement of cargo from origin to destination. Norvane is constantly rated as one of the top carriers under this contract that is governed by the strict confines of a by the customer fully developed QA program detailed in an associated Quality Assurance Surveillance Plan (QASP) document that defines how performance standards will be applied; frequency of surveillance; and minimum acceptable defect</p>
    </article>

    <div class="band band-right"></div>
    <h2 class="section-title" style="left:16px;top:299px">OUR PROJECTS</h2>
    <div class="photo hero-rig" role="img" aria-label="Offshore oil platform at sea under an evening sky"></div>
  </section>
</div>
</body>
</html>
```